Vantiqo custom business card design

Need a authentic, innovative business card design for a new mobile app business. I am uploading a few screen images from our app for you to view. I would like app design theme to match business card design. I can also send logo images.

```html
<!DOCTYPE html>
<html lang="en">
<head>
<meta charset="utf-8">
<title>Vantiqo Business Card</title>
<link rel="stylesheet" href="https://fonts.googleapis.com/css2?family=Montserrat:wght@500;600;800&family=Roboto:wght@400&display=swap">
<style>
  :root {
    --bg: #2b2b2d;
    --card-dark: #000000;
    --card-light: #ffffff;
    --purple: #66139a;
    --ink: #1f1f1f;
    --muted: #444444;
  }
  html, body {
    margin: 0;
    padding: 0;
    width: 1200px;
    height: 874px;
    overflow: hidden;
    background: var(--bg);
  }
  .canvas {
    position: relative;
    width: 1200px;
    height: 874px;
  }
  .card {
    position: absolute;
    left: 260px;
    width: 680px;
    height: 388px;
    overflow: hidden;
    box-shadow: 0 10px 30px rgba(0,0,0,0.45);
  }
  .card--back {
    top: 39px;
    background: var(--card-dark);
  }
  .card--front {
    top: 447px;
    background: var(--card-light);
  }
  .back-mark {
    position: absolute;
    left: 50%;
    top: 80px;
    width: 150px;
    height: 150px;
    margin-left: -75px;
    border-radius: 50%;
    background: var(--purple);
  }
  .back-wordmark {
    position: absolute;
    left: 0;
    right: 0;
    top: 246px;
    text-align: center;
    font-family: "Montserrat", sans-serif;
    font-weight: 800;
    font-size: 46px;
    color: var(--card-light);
    letter-spacing: 0.5px;
  }
  .contact {
    position: absolute;
    left: 48px;
    top: 40px;
    font-family: "Roboto", sans-serif;
    color: var(--muted);
  }
  .contact__name {
    margin: 0;
    font-family: "Montserrat", sans-serif;
    font-weight: 600;
    font-size: 24px;
    color: var(--purple);
    letter-spacing: 0.3px;
  }
  .contact__title {
    margin: 2px 0 16px;
    font-family: "Montserrat", sans-serif;
    font-weight: 500;
    font-size: 15px;
    color: var(--ink);
  }
  .contact__address {
    margin: 0 0 12px;
    font-size: 15px;
    line-height: 1.35;
  }
  .contact__list {
    list-style: none;
    margin: 0;
    padding: 0;
    font-size: 15px;
    line-height: 1.4;
  }
  .contact__list li {
    display: flex;
    align-items: center;
    gap: 8px;
  }
  .contact__icon {
    width: 13px;
    height: 13px;
    flex: none;
    fill: var(--purple);
  }
  .front-wordmark {
    position: absolute;
    left: 46px;
    bottom: 34px;
    margin: 0;
    font-family: "Montserrat", sans-serif;
    font-weight: 800;
    font-size: 54px;
    color: var(--ink);
  }
  .front-mark {
    position: absolute;
    left: 342px;
    top: 52px;
    width: 300px;
    height: 300px;
    border-radius: 50%;
    background: var(--purple);
  }
</style>
</head>
<body>
<main class="canvas">
  <section class="card card--back" aria-label="Card back">
    <div class="back-mark"></div>
    <div class="back-wordmark">Vantiqo</div>
  </section>

  <section class="card card--front" aria-label="Card front">
    <div class="contact">
      <h1 class="contact__name">MARA DELGADO</h1>
      <p class="contact__title">CEO/FOUNDER</p>
      <p class="contact__address">412 Larkspur Court<br>Juneau, Alaska 99801</p>
      <ul class="contact__list">
        <li>
          <svg class="contact__icon" viewBox="0 0 16 16" aria-hidden="true"><path d="M3.5 1 6 4 4.6 5.8c.9 2 2.6 3.7 4.6 4.6L11 9l3 2.5-1.6 2.8C7 14 2 9 1.7 3.6Z"/></svg>
          555 214 7830
        </li>
        <li>
          <svg class="contact__icon" viewBox="0 0 16 16" aria-hidden="true"><path d="M4 1h8v14H4Zm1.5 1.5v9h5v-9Z" fill-rule="evenodd"/></svg>
          555 309 6621
        </li>
        <li>
          <svg class="contact__icon" viewBox="0 0 16 16" aria-hidden="true"><path d="M4 1h7v4H4ZM1 6h14v7h-3v2H4v-2H1Zm4 5v3h6v-3Z" fill-rule="evenodd"/></svg>
          555 472 1185
        </li>
        <li>
          <svg class="contact__icon" viewBox="0 0 16 16" aria-hidden="true"><path d="M1 3h14v10H1Zm1.5 1.5L8 9l5.5-4.5Z" fill-rule="evenodd"/></svg>
          mara@vantiqo.com
        </li>
        <li>
          <svg class="contact__icon" viewBox="0 0 16 16" aria-hidden="true"><circle cx="8" cy="8" r="7"/></svg>
          www.vantiqo.com
        </li>
      </ul>
    </div>
    <p class="front-wordmark">Vantiqo</p>
    <div class="front-mark"></div>
  </section>
</main>
</body>
</html>
```